Sophisticated, clean website reflecting my feminine, playful side to sell my abstract art,

I need a website no more than 3 pages to showcase my paintings, a little about me and some contact info. I do abstracts so looking for something a little edgy, yet feminine and current.
Updates

Hi there, These are some artists websites that I Iike: Marnelvoss.com (I like how airy it is) peterwallombry.com garethpolvens.com (I like how it scrolls) I'll need a place for a photo ( a headshot-i do not have it yet so I'll need to be able to upload that later) as well as an area for my bio. Also, it's important that I will be able to upload any new photos and descriptions easily so it should be user friendly. Lastly, I like in a sunny place so would like to have this seem upbeat and playful as that is how i like to paint. thanks-I'm trying to upload my photos now -

Target Market(s)

ppl ages 35-70 who want large scale art for their homes

Industry/Entity Type

art

Coding

Coded - Design and coding required

Number of Pages Required

3 page

Colors

Designer to choose colors to be used in the design.

Requirements
Must have
• photos of my art, a place for my bio, be easy to reach me. tasteful-nothing too "in your face" -my clients are pretty high end and organized. They like clean lines
Nice to have
• sophisticated background, muted tones in the back-similar clean font throughout-no cursive
Should not have
• too many dark areas. Too many blocks of color. Too serious.

```html
<!DOCTYPE html>
<html lang="en">
<head>
<meta charset="utf-8">
<title>Maren Solbeck — Abstract Paintings</title>
<link rel="stylesheet" href="https://fonts.googleapis.com/css2?family=Lato:wght@300;400&family=Questrial&display=swap">
<style>
:root{
  --ink:#111111;
  --muted:#9a9a9a;
  --body:#3a3a3a;
  --rule:#d6d6d6;
  --paper:#ffffff;
  --paper-soft:#f5f5f6;
  --frame:#dcdcdc;
}
*{box-sizing:border-box;margin:0;padding:0}
html,body{width:1200px;height:2788px;overflow:hidden}
body{position:relative;font-family:"Questrial",sans-serif;color:var(--ink);
  background:linear-gradient(180deg,var(--paper) 0,var(--paper) 1950px,var(--paper-soft) 2400px,var(--paper-soft) 100%)}
.abs{position:absolute}

/* header */
.brand{top:26px;left:0;width:1200px;display:flex;justify-content:center;align-items:center;gap:16px}
.brand-square{width:44px;height:44px;background:var(--ink)}
.brand-name{font-family:"Lato",sans-serif;font-weight:300;font-size:45px;letter-spacing:1px;line-height:52px}
.header-rule{top:101px;left:0;width:1200px;height:2px;background:var(--rule)}
.main-nav{top:120px;left:0;width:1200px;font-size:16px;letter-spacing:.3px;line-height:20px}
.main-nav > .nav-link{position:absolute;top:0}
.main-nav .active::after{content:"";position:absolute;left:2px;right:2px;top:28px;height:2px;background:var(--ink)}
.nav-social{position:absolute;top:-6px;display:flex;align-items:center;gap:6px;white-space:nowrap}
.nav-social .dot{flex:none;width:32px;height:32px;border-radius:50%;background:var(--ink)}
.nav-social .handle{font-size:16px}

/* hero */
.hero{top:162px;left:0;width:1200px;height:648px;
  background:linear-gradient(120deg,#e9e4ea 0%,#3f8f3c 22%,#1f7a6a 38%,#d9d6dc 52%,#62a93e 64%,#c9b865 78%,#6a4b30 100%)}
.hero-controls{top:741px;left:901px;display:flex;align-items:center;gap:6px}
.play{font-family:"Lato",sans-serif;font-weight:400;font-size:19px;color:#fff;letter-spacing:1px;margin-right:18px;display:flex;align-items:center;gap:6px}
.ctrl{width:50px;height:32px;background:#fff;display:flex;align-items:center;justify-content:center}

/* section headings */
.section-title{left:0;width:1200px;text-align:center;font-family:"Lato",sans-serif;font-weight:400;font-size:48px;line-height:56px}
.section-title em{font-style:normal;color:var(--muted)}
.divider{left:0;width:1200px;display:flex;justify-content:center;align-items:center;gap:6px}
.divider i{display:block;width:32px;height:1.5px;background:var(--ink)}
.divider b{display:block;width:14px;height:14px;background:var(--ink)}

/* about */
.portrait-frame{top:1018px;left:81px;width:312px;height:334px;border:4px solid var(--frame);padding:6px;background:#fff}
.portrait{width:100%;height:100%;background:radial-gradient(ellipse at 50% 60%,#bdbdbd 0%,#d8d8d8 35%,#f6f6f6 70%)}
.bio{top:1027px;left:448px;width:657px;font-size:19px;line-height:27px;color:var(--body);text-align:justify}
.bio p{margin-bottom:15px}

/* gallery */
.painting-left{top:1697px;left:186px;width:140px;height:300px;background:linear-gradient(160deg,#d9d4c0 0%,#c9a11e 35%,#8b2a10 60%,#2c3658 100%)}
.painting-main{top:1645px;left:330px;width:572px;height:387px;background:linear-gradient(125deg,#3e2b4f 0%,#8a6fa6 25%,#d9cfe0 45%,#6b4b8c 60%,#b88a6a 78%,#e8dccc 100%)}
.painting-right{top:1697px;left:907px;width:125px;height:300px;background:linear-gradient(150deg,#e3c7b8 0%,#c06a6a 35%,#efd0d6 65%,#d8a0a8 100%)}
.arrow{top:1815px}

/* contact */
.contact-lead{top:2308px;left:0;width:1200px;text-align:center;font-size:22px}
.contact-item{top:2384px;width:320px;text-align:center;font-size:22px}
.contact-item .ring{width:72px;height:72px;margin:0 auto 20px;border-radius:50%;background:var(--ink);border:3px solid #fff;box-shadow:0 0 0 2px var(--ink);display:flex;align-items:center;justify-content:center}

/* footer */
.footer-rule{top:2628px;left:0;width:1200px;height:1px;background:var(--rule)}
.footer-nav{top:2668px;left:0;width:1200px;display:flex;justify-content:center;gap:77px;font-family:"Lato",sans-serif;font-size:18px}
.copyright{top:2713px;left:0;width:1200px;text-align:center;font-size:14px;color:var(--body)}
</style>
</head>
<body>

<header>
  <div class="abs brand"><span class="brand-square"></span><span class="brand-name">MAREN SOLBECK</span></div>
  <div class="abs header-rule"></div>
  <nav class="abs main-nav">
    <span class="nav-link active" style="left:185px">HOME</span>
    <span class="nav-link" style="left:344px">ABOUT ME</span>
    <span class="nav-link" style="left:542px">GALLERY</span>
    <span class="nav-link" style="left:727px">CONTACT</span>
    <div class="nav-social" style="left:912px"><span class="dot"></span><span class="handle">@msolbeckart</span></div>
  </nav>
</header>

<section>
  <div class="abs hero" role="img" aria-label="Close-up of an abstract painting in greens, teal and ochre brushstrokes"></div>
  <div class="abs hero-controls">
    <span class="play">PLAY <svg width="10" height="12" viewBox="0 0 10 12"><path d="M0 0L10 6L0 12Z" fill="#fff"/></svg></span>
    <span class="ctrl"><svg width="12" height="14" viewBox="0 0 12 14"><path d="M12 0L0 7L12 14Z" fill="#111"/></svg></span>
    <span class="ctrl"><svg width="12" height="14" viewBox="0 0 12 14"><path d="M0 0L12 7L0 14Z" fill="#111"/></svg></span>
  </div>
</section>

<section>
  <h2 class="abs section-title" style="top:893px">ABOUT <em>ME</em></h2>
  <div class="abs divider" style="top:961px"><i></i><b></b><i></i></div>
  <div class="abs portrait-frame"><div class="portrait" role="img" aria-label="Headshot portrait of the artist"></div></div>
  <div class="abs bio">
    <p>Lorem ipsum dolor sit amet, consectetur adipiscing elit, sed do eiusmod tempor incididunt ut labore et dolore magna aliqua. Ut enim ad minim veniam, quis nostrud exercitation</p>
    <p>Duis aute irure dolor in reprehenderit in voluptate velit esse cillum dolore eu fugiat nulla pariatur. Excepteur sint occaecat cupidatat non proident, sunt in culpa qui officia deserunt mollit anim id est laborum</p>
    <p>Sed ut perspiciatis unde pariatur. Excepteur sint occaecat cupidatat non proident, sunt in culpa qui officia deserunt mollit anim id est laborum.Sed ut persmollit anim id est laborum. Excepteur sint occaecat cupidatat non proident, sunt in culpa qui officia deserunt</p>
  </div>
</section>

<section>
  <h2 class="abs section-title" style="top:1485px">PAINTING <em>GALLERY</em></h2>
  <div class="abs divider" style="top:1549px"><i></i><b></b><i></i></div>
  <div class="abs painting-left" role="img" aria-label="Abstract painting in ochre, rust red and navy"></div>
  <div class="abs painting-main" role="img" aria-label="Featured abstract painting in purple, lavender and cream"></div>
  <div class="abs painting-right" role="img" aria-label="Abstract painting in pink and rose tones"></div>
  <svg class="abs arrow" style="left:96px" width="34" height="60" viewBox="0 0 34 60"><path d="M32 2L3 30L32 58" fill="none" stroke="#333" stroke-width="2"/></svg>
  <svg class="abs arrow" style="left:1106px" width="34" height="60" viewBox="0 0 34 60"><path d="M2 2L31 30L2 58" fill="none" stroke="#333" stroke-width="2"/></svg>
</section>

<section>
  <h2 class="abs section-title" style="top:2209px">CONTACT <em>US</em></h2>
  <div class="abs divider" style="top:2270px"><i></i><b></b><i></i></div>
  <p class="abs contact-lead">Please get in touch with me on below details.</p>
  <div class="abs contact-item" style="left:119px">
    <div class="ring"><svg width="34" height="34" viewBox="0 0 24 24"><path d="M6.6 3.5l2.6 3.2-1.6 2.2c1 2.2 3.2 4.4 5.5 5.5l2.2-1.6 3.2 2.6-1.6 3c-6.4-.3-12.5-6.4-12.8-12.8z" fill="none" stroke="#fff" stroke-width="1.2" stroke-linejoin="round"/></svg></div>
    (123) 456 7890
  </div>
  <div class="abs contact-item" style="left:446px">
    <div class="ring"><svg width="34" height="26" viewBox="0 0 34 26"><rect x="1" y="1" width="32" height="24" fill="none" stroke="#fff" stroke-width="1.5"/><path d="M1 1L17 15L33 1M1 25L13 12M33 25L21 12" fill="none" stroke="#fff" stroke-width="1.5"/></svg></div>
    marensolbeck@info.com
  </div>
  <div class="abs contact-item" style="left:768px">
    <div class="ring"></div>
    @msolbeckart
  </div>
</section>

<footer>
  <div class="abs footer-rule"></div>
  <nav class="abs footer-nav"><span>HOME</span><span>ABOUT ME</span><span>GALLERY</span><span>CONTACT</span></nav>
  <p class="abs copyright">© 2022 Maren Solbeck &nbsp; All Rights Reserved</p>
</footer>

</body>
</html>
```